Veldmark Supplies Business Card

Professional business card that stand out to our potential customers. Front and back with clean modern design

Industry/Entity Type

Oil and gas

Contact Information for Business Card

Name, address, website , office phone and cell number

Requirements
Must have
• Editable files for each employee

```html
<!DOCTYPE html>
<html lang="en">
<head>
<meta charset="utf-8">
<title>Veldmark Supplies Business Card</title>
<link href="https://fonts.googleapis.com/css2?family=Montserrat:wght@400;500;700;800&display=swap" rel="stylesheet">
<style>
  :root {
    --blue: #0aaed3;
    --blue-deep: #0790b2;
    --red: #ec1c24;
    --ink: #1c1c1c;
    --paper: #ffffff;
    --backdrop: #ecebe8;
  }
  * { box-sizing: border-box; margin: 0; padding: 0; }
  html, body { width: 1200px; height: 931px; overflow: hidden; }
  body {
    background: var(--backdrop);
    font-family: "Montserrat", sans-serif;
    position: relative;
  }
  .card {
    position: absolute;
    width: 660px;
    height: 377px;
    border-radius: 22px;
    overflow: hidden;
    box-shadow: 0 10px 24px rgba(0,0,0,0.18);
  }
  /* Back side */
  .card-back { left: 90px; top: 60px; background: var(--blue); }
  .back-brand {
    position: absolute; left: 0; right: 0; top: 150px;
    display: flex; align-items: center; justify-content: center; gap: 16px;
  }
  .brand-square { width: 34px; height: 34px; background: var(--blue-deep); }
  .back-brand .brand-name {
    font-weight: 800; font-size: 34px; letter-spacing: 2px;
    text-transform: uppercase; color: var(--blue-deep);
  }
  /* Front side */
  .card-front { left: 450px; top: 490px; background: var(--paper); }
  .front-brand {
    position: absolute; right: 40px; top: 52px;
    display: flex; align-items: center; gap: 12px;
  }
  .front-brand .brand-square { width: 26px; height: 26px; background: var(--blue); }
  .front-brand .brand-name {
    font-weight: 800; font-size: 24px; letter-spacing: 1.5px;
    text-transform: uppercase; color: var(--red);
  }
  .person { position: absolute; left: 40px; top: 150px; }
  .person-name { font-weight: 800; font-size: 30px; color: var(--red); line-height: 1.1; }
  .person-title { font-weight: 400; font-size: 17px; color: var(--ink); margin-top: 4px; }
  .divider {
    position: absolute; left: 40px; right: 30px; top: 222px;
    height: 1.5px; background: var(--red);
  }
  .contacts { position: absolute; left: 48px; top: 234px; list-style: none; }
  .contacts li {
    display: flex; align-items: center; gap: 12px;
    font-size: 15px; color: var(--ink); line-height: 22px;
  }
  .contacts svg { width: 15px; height: 15px; fill: var(--blue); flex: none; }
  .address {
    position: absolute; right: 36px; top: 236px;
    font-size: 14px; line-height: 20px; color: var(--ink); text-align: right;
  }
  .band { position: absolute; bottom: 0; height: 20px; }
  .band-blue { left: 0; width: 440px; background: var(--blue); }
  .band-red { left: 452px; right: 0; background: var(--red); height: 34px; }
  .band-blue-edge { left: 0; width: 440px; bottom: 0; }
</style>
</head>
<body>

  <section class="card card-back" aria-label="Card back">
    <div class="back-brand">
      <span class="brand-square"></span>
      <span class="brand-name">Veldmark Supplies</span>
    </div>
  </section>

  <section class="card card-front" aria-label="Card front">
    <div class="front-brand">
      <span class="brand-square"></span>
      <span class="brand-name">Veldmark Supplies</span>
    </div>

    <div class="person">
      <p class="person-name">Tomas Rellan</p>
      <p class="person-title">President</p>
    </div>
    <div class="divider"></div>

    <ul class="contacts">
      <li>
        <svg viewBox="0 0 16 16"><path d="M2 5c0-2 3-3 6-3s6 1 6 3v1h-3V5H5v1H2zM4 7h8l2 6H2z"/></svg>
        +1.555.210.4400 x123
      </li>
      <li>
        <svg viewBox="0 0 16 16"><path d="M4 1l3 3-2 2c1 2 3 4 5 5l2-2 3 3-2 3C7 15 1 9 1 3z"/></svg>
        +1.555.318.7720
      </li>
      <li>
        <svg viewBox="0 0 16 16"><path d="M1 3h14v10H1zM2 4l6 5 6-5"/></svg>
        info@veldmarksupply.com
      </li>
      <li>
        <svg viewBox="0 0 16 16"><circle cx="8" cy="8" r="7"/></svg>
        www.veldmarksupply.com
      </li>
    </ul>

    <p class="address">42 Ridgeline Plaza<br>Harlow Falls, NJ 07811 USA</p>

    <div class="band band-blue"></div>
    <div class="band band-red"></div>
  </section>

</body>
</html>
```